Strategy and Technology Consulting - Our Story and Values Page

Interior Page design – Our History and Our Values

Our homepage has been designed and we are looking for a design for one of the interior pages. This interior page tells the story of Our History and Our Values

Because the homepage has been designed, we would like this interior page to reflect the design of the homepage without being a mirror image of the homepage.

This site will be implemented in WordPress using the Elementor framework.

Font: Poppins medium and Poppins dark
Illustrations: Our homepage illustrations were designed by “Brelin 1974” on Quillmark. Compatible original or stock illustrations are welcome. Stock photography is also welcome. Brelin is also available through Brelin Tosamek on Ravolo

Uploaded Files
• Homepage design – this is the design we will use for our homepage. Contest entries should reflect this basic style but should be distinctly different from the homepage.
• Our History and Our Values – Wireframe – the basic layout of the page we are looking for.
• Our History and Our Values – Word document with the text supporting the wireframe.
• Color Palette – please use colors compatible with the palette attached.

Our Story - timeline
There is a timeline element in the wireframe. The wireframe displays this as a series of chevrons (arrows), but it does not need to be. Creativity in display of the timeline is appreciated.

Our Values
If you look at the Word document, you will see that there are a lot of words on the page. The winning design will present the information in a way that engages the user without overwhelming them with too much to read. For example, they may click on a value and see more information.

Target Market(s)

CIO's and Technology Executives

Number of Pages Required

1 page

Font styles to use
Sans Serif
Other font styles liked:
• Poppin

Requirements
Must have
• A timeline element, all of our values
Nice to have
• Clever timeline display

```html
<!DOCTYPE html>
<html lang="en">
<head>
<meta charset="utf-8">
<title>Veltrane – Our Story &amp; Values</title>
<link href="https://fonts.googleapis.com/css2?family=Poppins:wght@300;400;500;600;700;800&display=swap" rel="stylesheet">
<style>
:root{
  --gold:#e9b30f;
  --blue:#155694;
  --title-blue:#1b5aa0;
  --ink:#2b2f38;
  --muted:#5e6b7d;
  --pale:#f3f6fc;
  --line:#e3e8f1;
  --slate:#3f4f6a;
  --slate-dark:#2f3b50;
  --white:#fff;
}
*{box-sizing:border-box;margin:0;padding:0}
html,body{width:1200px;height:3429px;overflow:hidden}
body{position:relative;font-family:"Poppins",sans-serif;color:var(--ink);background:var(--white)}
.abs{position:absolute}

/* header */
.site-header{position:absolute;left:0;top:0;width:1200px;height:90px;border-bottom:1px solid var(--line);background:var(--white)}
.brand{position:absolute;left:106px;top:18px;font-family:"Poppins",sans-serif;font-weight:300;font-size:42px;color:#8b97a6;letter-spacing:.5px}
.main-nav{position:absolute;left:540px;top:36px;display:flex;gap:22px;align-items:center;font-size:12px;font-weight:600;color:#3a4557}
.main-nav span::after{content:"";display:inline-block;width:5px;height:5px;border-right:1.5px solid #3a4557;border-bottom:1.5px solid #3a4557;transform:rotate(45deg);margin-left:6px;position:relative;top:-3px}
.btn-gold{position:absolute;background:var(--gold);color:var(--white);font-weight:700;font-size:11px;border-radius:30px;display:flex;align-items:center;justify-content:center;letter-spacing:.3px}
.header-cta{left:963px;top:26px;width:126px;height:36px}

.section-title{position:absolute;left:0;width:1200px;text-align:center;font-weight:700;font-size:43px;color:var(--gold)}

/* timeline */
.era{position:absolute;top:226px;width:281px;height:280px;background:var(--white);border:1px solid var(--line);box-shadow:6px 8px 18px rgba(30,50,90,.1)}
.era-head{height:47px;background:var(--blue);color:var(--white);font-weight:600;font-size:19px;padding:11px 17px}
.era ul{list-style:none;padding:22px 14px 0 17px;font-size:15px;line-height:28px;color:var(--ink)}
.era li{position:relative;padding-left:30px}
.era li.sub{padding-left:47px}
.era li.sub::before{content:"–";position:absolute;left:30px}
.era li svg{position:absolute;left:0;top:8px}
.era-arrow{position:absolute;top:331px;width:48px;height:48px;border-radius:50%;background:var(--gold);display:flex;align-items:center;justify-content:center}

/* values */
.values-bg{position:absolute;left:0;top:540px;width:1200px;height:2300px}
.value{position:absolute;width:901px;height:253px;background:var(--white);border:1px solid var(--line)}
.value.left{left:112px}
.value.right{left:189px}
.value h3{position:absolute;top:52px;font-weight:500;font-size:19px;color:var(--title-blue)}
.value p{position:absolute;top:88px;font-size:15.5px;line-height:28.3px;color:var(--ink)}
.value.left h3,.value.left p{left:192px;width:670px}
.value.right h3,.value.right p{left:29px;width:660px}
.value-icon{position:absolute;top:30px;width:104px;height:104px;border-radius:4px;background:linear-gradient(135deg,#dfe6fb 0%,#f4f6fe 60%,#fff 100%);border:1.5px solid #c8d4f3}
.value.left .value-icon{left:30px}
.value.right .value-icon{left:749px;top:60px}

/* newsletter & footer */
.footer-bg{position:absolute;left:0;top:2700px;width:1200px;height:670px}
.newsletter{position:absolute;left:137px;top:2715px;width:923px;height:207px;border-radius:104px;background:var(--gold)}
.newsletter h2{position:absolute;left:81px;top:54px;font-weight:800;font-size:33px;color:var(--white)}
.newsletter p{position:absolute;left:81px;top:111px;font-size:15px;line-height:19px;color:var(--white);font-weight:500;width:420px}
.subscribe{position:absolute;left:549px;top:82px;width:320px;height:45px;border-radius:25px;background:var(--white);display:flex;align-items:center;padding-left:22px;font-size:12.5px;color:#8a94a4;gap:8px}
.subscribe .send{position:absolute;right:5px;top:4px;width:37px;height:37px;border-radius:50%;background:#9aa7b8;display:flex;align-items:center;justify-content:center}

.footer-brand{position:absolute;left:117px;top:3100px;font-weight:300;font-size:60px;color:#e4e9f0}
.social{position:absolute;top:3179px;width:42px;height:42px;border-radius:50%;background:rgba(255,255,255,.22)}
.footer-cta{left:214px;top:3245px;width:131px;height:37px}
.fcol{position:absolute;top:3076px;color:var(--white)}
.fcol h4{font-weight:700;font-size:21px;margin-bottom:13px}
.fcol ul{list-style:none;font-size:13px;color:#e8edf4}
.fcol li{height:31.2px}
.fcol li::before{content:"›";margin-right:6px}
.contact-item{position:relative;padding-left:23px;font-size:13px;line-height:17px;color:#e8edf4;margin-bottom:17px}
.contact-item svg{position:absolute;left:0;top:2px}
.bottom-bar{position:absolute;left:0;top:3368px;width:1200px;height:61px;background:var(--slate-dark);color:var(--white);font-size:13.5px;font-weight:500;display:flex;align-items:center;justify-content:center}
.chat{position:absolute;left:1135px;top:3342px;width:48px;height:48px;border-radius:50%;background:var(--gold);display:flex;align-items:center;justify-content:center;box-shadow:0 4px 10px rgba(0,0,0,.2)}
</style>
</head>
<body>

<header class="site-header">
  <div class="brand">Veltrane</div>
  <nav class="main-nav">
    <svg width="16" height="14" viewBox="0 0 16 14"><path d="M8 0 0 7h2v7h4V9h4v5h4V7h2z" fill="#8fa3b8"/></svg>
    <span>ABOUT US</span><span>SERVICES</span><span>INSIGHTS</span><span>JOIN US</span>
  </nav>
  <div class="btn-gold header-cta">CONTACT US</div>
</header>

<h1 class="section-title" style="top:126px">Our Story</h1>

<svg width="0" height="0" style="position:absolute">
  <defs>
    <symbol id="tick" viewBox="0 0 14 14"><circle cx="7" cy="7" r="5.8" fill="none" stroke="#e9b30f" stroke-width="1.6"/><path d="M4.4 7.2 6.3 9l3.3-3.6" fill="none" stroke="#e9b30f" stroke-width="1.6"/></symbol>
  </defs>
</svg>

<section class="timeline">
  <article class="era" style="left:112px">
    <div class="era-head">2017 – 2019</div>
    <ul>
      <li><svg width="14" height="14"><use href="#tick"/></svg>Growth Strategy Focus</li>
      <li><svg width="14" height="14"><use href="#tick"/></svg>Consistent, Modest Growth</li>
      <li><svg width="14" height="14"><use href="#tick"/></svg>Preliminary Focus on Technology</li>
      <li><svg width="14" height="14"><use href="#tick"/></svg>Eureka! &nbsp;Implementing strategy is hard.</li>
    </ul>
  </article>
  <div class="era-arrow" style="left:392px"><svg width="14" height="18"><path d="M2 1l11 8-11 8z" fill="#1d1d1d"/></svg></div>

  <article class="era" style="left:459px">
    <div class="era-head">2020 – 2021</div>
    <ul>
      <li><svg width="14" height="14"><use href="#tick"/></svg>Pandemic Pauses Growth</li>
      <li><svg width="14" height="14"><use href="#tick"/></svg>Rethinking :</li>
      <li class="sub">the business model</li>
      <li class="sub">the delivery model</li>
    </ul>
  </article>
  <div class="era-arrow" style="left:740px"><svg width="14" height="18"><path d="M2 1l11 8-11 8z" fill="#1d1d1d"/></svg></div>

  <article class="era" style="left:806px">
    <div class="era-head">2022 and Onward</div>
    <ul>
      <li><svg width="14" height="14"><use href="#tick"/></svg>Leadership Team for Focus on Essential Areas</li>
      <li><svg width="14" height="14"><use href="#tick"/></svg>Rapid Growth</li>
      <li><svg width="14" height="14"><use href="#tick"/></svg>•Customer Success</li>
    </ul>
  </article>
</section>

<svg class="values-bg" viewBox="0 0 1200 2300" preserveAspectRatio="none">
  <path d="M0 152C150 185 250 120 400 70 560 15 700 0 860 40 1000 75 1100 130 1200 178V2300H0Z" fill="#f3f6fc"/>
</svg>

<h2 class="section-title" style="top:640px">Our Values</h2>

<section class="values">
  <article class="value left" style="top:741px">
    <div class="value-icon" role="img" aria-label="Line icon of a group of people above a diamond"></div>
    <h3>The Value of Every Human. Regardless.</h3>
    <p>Each person's unique experiences and perspectives add vibrant hues to the tapestry of our shared existence.&nbsp; In a world where diversity paints the canvas of humanity, true beauty is found in recognizing the inherent and incalculable value of every human being.</p>
  </article>
  <article class="value right" style="top:1015px">
    <h3>Collaboration</h3>
    <p>Collaboration in work transforms individual endeavors into symphonies of collective achievement. Through collaboration, diverse talents converge, fostering a rich exchange of ideas that amplifies creativity, accelerates progress, and brings forth solutions beyond what a single mind could conceive.</p>
    <div class="value-icon" role="img" aria-label="Line icon of two hands joining puzzle pieces"></div>
  </article>
  <article class="value left" style="top:1298px">
    <div class="value-icon" role="img" aria-label="Line icon of a heart with a flame inside"></div>
    <h3>Passion</h3>
    <p>Passion Passion infuses our work with energy, transforming routine tasks into opportunities for creativity and innovation. Fueled by passion, individuals become unstoppable forces, driven to overcome challenges and achieve remarkable outcomes that benefit them and inspire those around them</p>
  </article>
  <article class="value right" style="top:1573px">
    <h3>Excellence</h3>
    <p>Excellence &nbsp; Excellence isn't a destination; it's a continuous journey of refinement and growth. Striving for excellence cultivates a culture of continuous improvement, fostering innovation, credibility, and a lasting impact that resonates far beyond the immediate task.</p>
    <div class="value-icon" role="img" aria-label="Line icon of a star badge with a thumbs up"></div>
  </article>
  <article class="value left" style="top:1847px">
    <div class="value-icon" role="img" aria-label="Line icon of a raised clenched fist"></div>
    <h3>Tenacity</h3>
    <p>Tenacity is the unwavering anchor that keeps us grounded amidst adversity, propelling us forward when faced with obstacles. The resilience to persist, adapt, and learn from setbacks leads to the mastery of skills and the fulfillment of ambitious goals.</p>
  </article>
  <article class="value right" style="top:2129px">
    <h3>Solution Mindset</h3>
    <p>A solution mindset is the compass that directs our focus from problems to possibilities. It empowers us to navigate challenges with a proactive mindset, igniting a journey of exploration and innovation that not only resolves issues but also paves the way for continuous growth and success.</p>
    <div class="value-icon" role="img" aria-label="Line icon of a light bulb made of puzzle pieces"></div>
  </article>
  <article class="value left" style="top:2403px">
    <div class="value-icon" role="img" aria-label="Line icon of hands holding a heart below books"></div>
    <h3>Generosity</h3>
    <p>Generosity creates a virtuous cycle of goodwill, fostering a sense of unity and shared purpose among colleagues. By freely sharing knowledge, support, and resources, we uplift those around us and contribute to a collaborative environment where collective achievements flourish.</p>
  </article>
</section>

<svg class="footer-bg" viewBox="0 0 1200 670" preserveAspectRatio="none">
  <defs>
    <linearGradient id="slate" x1="0" y1="1" x2="1" y2="0">
      <stop offset="0" stop-color="#61789a"/><stop offset=".5" stop-color="#45556f"/><stop offset="1" stop-color="#3c4a62"/>
    </linearGradient>
  </defs>
  <path d="M0 40C120 70 200 140 300 250 380 330 460 300 560 240 680 170 760 230 860 280 960 330 1060 270 1200 200V670H0Z" fill="#d5dae2"/>
  <path d="M0 45C120 75 200 150 300 265 380 345 460 315 560 255 680 185 760 245 860 295 960 345 1060 285 1200 212V670H0Z" fill="url(#slate)"/>
</svg>

<section class="newsletter">
  <h2>Subscribe Our Newsletter</h2>
  <p>Subscribe our newsletter to receive the latest news and exclusive offers every week, No spam.</p>
  <div class="subscribe">
    <svg width="14" height="10"><rect x=".5" y=".5" width="13" height="9" fill="#9aa7b8"/><path d="M.5.5 7 5.5 13.5.5" fill="none" stroke="#fff"/></svg>
    Enter email address
    <div class="send"><svg width="16" height="16" viewBox="0 0 16 16"><path d="M15 1 1 7l5 2 2 5z" fill="#fff"/></svg></div>
  </div>
</section>

<footer>
  <div class="footer-brand">Veltrane</div>
  <div class="social" style="left:176px" aria-label="Social link"></div>
  <div class="social" style="left:226px" aria-label="Social link"></div>
  <div class="social" style="left:277px" aria-label="Social link"></div>
  <div class="social" style="left:328px" aria-label="Social link"></div>
  <div class="btn-gold footer-cta">CONTACT US</div>

  <div class="fcol" style="left:491px">
    <h4>Quick links</h4>
    <ul><li>Home</li><li>About Us</li><li>Services</li><li>Insights</li><li>Join Us</li><li>Contact Us</li></ul>
  </div>
  <div class="fcol" style="left:668px">
    <h4>Our Services</h4>
    <ul><li>Business Transformation</li><li>ERP Implementations</li><li>ERP Solutions</li><li>BI and Data</li><li>Building the Right Team...</li></ul>
  </div>
  <div class="fcol" style="left:899px">
    <h4>Contact info</h4>
    <div class="contact-item"><svg width="13" height="10"><rect width="13" height="10" fill="#e9b30f"/><path d="M0 0l6.5 5L13 0" fill="none" stroke="#3f4f6a"/></svg>Email:<br>hello@veltrane-consult.com</div>
    <div class="contact-item"><svg width="13" height="13" viewBox="0 0 13 13"><path d="M2 1l2.5-.5 1.5 3-1.5 1.2a7 7 0 0 0 3.8 3.8L9.5 7l3 1.5L12 11c-5 1-11-5-10-10z" fill="#e9b30f"/></svg>Phone:<br>+44 113 555 0192</div>
    <div class="contact-item"><svg width="11" height="14" viewBox="0 0 11 14"><path d="M5.5 0A5.5 5.5 0 0 0 0 5.5C0 9 5.5 14 5.5 14S11 9 11 5.5A5.5 5.5 0 0 0 5.5 0z" fill="#e9b30f"/><circle cx="5.5" cy="5.5" r="2" fill="#3f4f6a"/></svg>Location:<br>Some address line goes<br>here city name</div>
  </div>

  <div class="bottom-bar">© Veltrane Design 2023, All Rights Reserved</div>
  <div class="chat"><svg width="24" height="20" viewBox="0 0 24 20"><path d="M12 1C6 1 1 4.8 1 9.5c0 2.6 1.5 4.9 3.9 6.4L4 19l4.2-2.2c1.2.3 2.5.5 3.8.5 6 0 11-3.8 11-8.5S18 1 12 1z" fill="#fff"/><circle cx="7.5" cy="9.5" r="1.4" fill="#e9b30f"/><circle cx="12" cy="9.5" r="1.4" fill="#e9b30f"/><circle cx="16.5" cy="9.5" r="1.4" fill="#e9b30f"/></svg></div>
</footer>

</body>
</html>
```